Business Card - Tidal Lanes

Need Business Card design for company named Tidal Lanes. Software development focused mainly on Brindle Orvix & Zelt Apps. I've attached our logo with both a black and white background. Please add trademark symbol to logo when using.

```html
<!DOCTYPE html>
<html lang="en">
<head>
<meta charset="utf-8">
<title>Tidal Lanes – Business Card</title>
<link rel="stylesheet" href="https://fonts.googleapis.com/css2?family=Source+Sans+3:wght@400;600;700&display=swap">
<style>
  :root {
    --stage: #e4e5ea;
    --card: #050505;
    --white: #ffffff;
    --muted: #bdbdbd;
    --orange: #f7943a;
    --amber: #f6a01a;
    --yellow: #fbbd19;
    --red: #d9202b;
    --ink-shadow: rgba(0,0,0,0.22);
  }
  * { margin: 0; padding: 0; box-sizing: border-box; }
  html, body {
    width: 1200px; height: 987px; overflow: hidden;
    background: var(--stage);
    font-family: "Source Sans 3", "Myriad Pro", sans-serif;
  }
  .canvas { position: relative; width: 1200px; height: 987px; }
  .card {
    position: absolute;
    width: 760px; height: 434px;
    background: var(--card);
    border-radius: 38px;
    overflow: hidden;
    box-shadow: 0 14px 30px var(--ink-shadow);
  }
  .card--back { left: 380px; top: 56px; }
  .card--front { left: 60px; top: 500px; }

  /* back */
  .back-brand {
    position: absolute; left: 0; right: 0; top: 150px;
    text-align: center;
  }
  .wordmark {
    color: var(--white); font-weight: 700; letter-spacing: -1px;
    display: inline-flex; align-items: center; gap: 14px;
  }
  .wordmark__dot { width: 18px; height: 18px; border-radius: 50%; background: var(--orange); }
  .back-brand .wordmark { font-size: 76px; line-height: 1; }
  .back-brand .site { margin-top: 18px; color: var(--muted); font-size: 22px; letter-spacing: 1px; }

  /* front */
  .accent-tab { position: absolute; left: 0; top: 40px; width: 14px; height: 52px; background: var(--amber); }
  .person { position: absolute; left: 56px; top: 40px; }
  .person__name { color: var(--orange); font-weight: 700; font-size: 26px; line-height: 1; }
  .person__title { color: var(--white); font-size: 18px; margin-top: 2px; }
  .address { position: absolute; left: 118px; top: 128px; color: var(--white); font-size: 20px; }
  .phones { position: absolute; left: 40px; top: 190px; list-style: none; }
  .phones li { color: var(--white); font-size: 20px; display: flex; align-items: center; gap: 10px; height: 30px; }
  .phones svg { width: 18px; height: 18px; }
  .bands { position: absolute; left: 0; top: 0; width: 760px; height: 434px; }
  .band-site { position: absolute; left: 40px; top: 306px; color: var(--white); font-size: 18px; letter-spacing: .5px; }
  .front-brand { position: absolute; right: 70px; top: 210px; }
  .front-brand .wordmark { font-size: 52px; line-height: 1; }
</style>
</head>
<body>
<main class="canvas">

  <section class="card card--back" aria-label="Card back">
    <div class="back-brand">
      <div class="wordmark"><span class="wordmark__dot"></span>Tidal Lanes</div>
      <div class="site">www.tidallanes.com</div>
    </div>
  </section>

  <section class="card card--front" aria-label="Card front">
    <svg class="bands" viewBox="0 0 760 434" aria-hidden="true">
      <defs>
        <linearGradient id="sweep" x1="0" x2="1" y1="0" y2="0">
          <stop offset="0" stop-color="#fbbd19"/>
          <stop offset="0.55" stop-color="#f9a82a"/>
          <stop offset="1" stop-color="#f7943a"/>
        </linearGradient>
      </defs>
      <path d="M0,292 L330,292 C372,292 382,338 428,338 L0,338 Z" fill="#d9202b"/>
      <path d="M0,338 L428,338 C470,338 478,376 520,376 L760,376 L760,434 L0,434 Z" fill="url(#sweep)"/>
    </svg>

    <span class="accent-tab"></span>
    <div class="person">
      <div class="person__name">Your Name</div>
      <div class="person__title">Title</div>
    </div>
    <p class="address">2410 Harbor View Rd, Seabrook, FL 33790</p>
    <ul class="phones">
      <li>
        <svg viewBox="0 0 18 18" aria-hidden="true"><rect x="5" y="1" width="8" height="16" rx="2" fill="#f6a01a"/><rect x="7" y="3" width="4" height="7" fill="#050505"/></svg>
        727-555-0148
      </li>
      <li>
        <svg viewBox="0 0 18 18" aria-hidden="true"><path d="M2,12 C2,8 5,6 9,6 C13,6 16,8 16,12 L16,14 L2,14 Z" fill="#f6a01a"/><rect x="7" y="3" width="4" height="3" fill="#f6a01a"/></svg>
        727-555-0193
      </li>
    </ul>
    <p class="band-site">www.tidallanes.com</p>

    <div class="front-brand">
      <div class="wordmark"><span class="wordmark__dot"></span>Tidal Lanes</div>
    </div>
  </section>

</main>
</body>
</html>
```